Flyer Design & Business Cards

I have tried to make up some flyer and have attached them as info with what we would like included. I would like them made to look more professional and I would like business cards along the same line.

Industry/Entity Type

Business

```html
<!DOCTYPE html>
<html lang="en">
<head>
<meta charset="utf-8">
<title>Eastmere Inn – Business Cards</title>
<link href="https://fonts.googleapis.com/css2?family=Open+Sans:wght@400;700&family=Uncial+Antiqua&display=swap" rel="stylesheet">
<style>
  :root {
    --sea-blue: #135d82;
    --gold: #f5ac2d;
    --accent-red: #c8262f;
    --backdrop: #d9d9d9;
    --photo-stone: #6f6a63;
    --photo-sky: #8fb8e0;
    --photo-fire: #c9772a;
    --photo-bottles: #5a3a2e;
    --photo-shelf: #7a5a45;
    --art-light: #a9dcf3;
    --art-mid: #6fb6de;
  }
  * { box-sizing: border-box; margin: 0; padding: 0; }
  html, body {
    width: 1200px; height: 869px; overflow: hidden;
    background: var(--backdrop);
    font-family: "Open Sans", Calibri, sans-serif;
  }
  .canvas { position: relative; width: 1200px; height: 869px; }

  .card {
    position: absolute;
    background: var(--sea-blue);
    box-shadow: 0 2px 6px rgba(0,0,0,.25);
    color: var(--gold);
    overflow: hidden;
  }
  .card--front { left: 64px; top: 66px; width: 640px; height: 356px; }
  .card--back  { left: 498px; top: 454px; width: 638px; height: 356px; }

  /* front: photo collage */
  .photo { position: absolute; }
  .photo--building { left: 0; top: 0; width: 245px; height: 220px;
    background: linear-gradient(180deg, var(--photo-sky) 0%, #7d8c98 35%, var(--photo-stone) 55%, #8a8a86 100%); }
  .photo--stove { left: 0; top: 223px; width: 126px; height: 133px;
    background: linear-gradient(135deg, #3b3530 0%, var(--photo-fire) 60%, #b39066 100%); }
  .photo--bottles { left: 129px; top: 223px; width: 116px; height: 86px;
    background: linear-gradient(90deg, var(--photo-bottles), #8a6a58 60%, #4a3a35); }
  .photo--shelf { left: 129px; top: 312px; width: 116px; height: 44px;
    background: linear-gradient(180deg, var(--photo-shelf), #3a2a22); }
  .divider-stripe { position: absolute; left: 245px; top: 0; width: 4px; height: 356px; background: var(--accent-red); }

  .ornament {
    position: absolute; width: 46px; height: 22px;
    background: var(--gold); border-radius: 11px; opacity: .9;
  }
  .frame { position: absolute; left: 0; top: 0; }

  .inn-name {
    position: absolute; left: 274px; top: 72px; width: 346px; text-align: center;
    font-family: "Uncial Antiqua", serif;
    font-weight: 400; font-size: 46px; line-height: 52px;
  }
  .address {
    position: absolute; left: 274px; top: 211px; width: 346px; text-align: center;
    font-size: 24px; line-height: 27.5px;
  }

  /* back */
  .illustration-area {
    position: absolute; left: 46px; top: 90px; width: 224px; height: 164px;
    background: linear-gradient(180deg, var(--art-light), var(--art-mid));
  }
  .owners {
    position: absolute; left: 298px; top: 75px; width: 300px; text-align: center;
    font-weight: 700; font-size: 38px; line-height: 46px;
  }
  .owners .joiner { font-size: 27px; }
  .contact {
    position: absolute; left: 298px; top: 178px; width: 300px; text-align: center;
    font-size: 27px; line-height: 31px;
  }
  .ornament--center { left: 398px; top: 264px; width: 100px; height: 20px; border-radius: 10px; }
</style>
</head>
<body>
<div class="canvas">

  <section class="card card--front">
    <div class="photo photo--building" role="img" aria-label="Photo of the stone-built inn under a blue sky"></div>
    <div class="photo photo--stove" role="img" aria-label="Photo of a wood-burning stove with a lit fire"></div>
    <div class="photo photo--bottles" role="img" aria-label="Photo of gin bottles on the bar shelf"></div>
    <div class="photo photo--shelf" role="img" aria-label="Photo of bottles along the bar"></div>
    <div class="divider-stripe"></div>

    <svg class="frame" width="640" height="356" aria-hidden="true">
      <path d="M282 84 V166 M612 84 V166" stroke="var(--gold)" stroke-width="2" fill="none"/>
    </svg>
    <div class="ornament" role="img" aria-label="Scroll ornament" style="left:268px;top:62px;"></div>
    <div class="ornament" role="img" aria-label="Scroll ornament" style="left:580px;top:62px;"></div>
    <div class="ornament" role="img" aria-label="Scroll ornament" style="left:268px;top:168px;"></div>
    <div class="ornament" role="img" aria-label="Scroll ornament" style="left:580px;top:168px;"></div>

    <h1 class="inn-name">Eastmere<br>Inn</h1>

    <p class="address">Eastmere Inn<br>Baile Mhor Tarbert<br>Isle of Harvay<br>HS9 4QX</p>
  </section>

  <section class="card card--back">
    <svg class="frame" width="638" height="356" aria-hidden="true">
      <line x1="62" y1="30" x2="574" y2="30" stroke="var(--gold)" stroke-width="2"/>
      <line x1="62" y1="328" x2="574" y2="328" stroke="var(--gold)" stroke-width="2"/>
    </svg>
    <div class="ornament" role="img" aria-label="Scroll ornament" style="left:14px;top:19px;"></div>
    <div class="ornament" role="img" aria-label="Scroll ornament" style="left:578px;top:19px;"></div>
    <div class="ornament" role="img" aria-label="Scroll ornament" style="left:14px;top:317px;"></div>
    <div class="ornament" role="img" aria-label="Scroll ornament" style="left:578px;top:317px;"></div>

    <div class="illustration-area" role="img" aria-label="Illustration of a tall sailing ship at sea"></div>

    <h2 class="owners">Morag <span class="joiner">and</span> Ewan<br>Fraser</h2>
    <p class="contact">01234 567890<br>www.eastmereinn.com</p>
    <div class="ornament ornament--center" role="img" aria-label="Scroll ornament"></div>
  </section>

</div>
</body>
</html>
```